Coastal Learner Bureau business cards

Australian company about to start offering its services. We recruit international students to come to study English, vocational education and postgraduate courses in Australia. We help them find the institution and select the right city they want to come to Australia. We are a young, online oriented and supportive agency. Our clients are between 18 and 35 years old, mainly University students, young professionals or people with work experience. We provide much more information that any other agency offer. We administrate a Facebook group with more than 11.000 members that daily ask questions about general information when coming to Australia, while they are here and even after they leave the country

Target Market(s)

International students from South America, Central America and Europe

Industry/Entity Type

Student

Contact Information for Business Card

Tomas Bilbrea
Managing Director
tomas@kelvarin.com.au
www.kelvoria.com.au
+61 491058264
Melbourne, Australia

Font styles to use
Serif
Sans Serif

Colors

Designer to choose colors to be used in the design.

Requirements
Must have
• Horizontal design
• Standard business card size and shape. If font uses green or yellow colours, they will have to match the ones from the logo
Nice to have
• UPDATE: Use the contents of the green image to design one of the card sides. Use our logo in the background of that side as watermark.
• Passport image, or immigration stamps. A picture of the Yarra River (from Melbourne) would be cool as well.
Should not have
• Non-standard business card size and shape
• Not black as the background colour of any sides as we are not a VIP agency or a hight class service. We are orientes to young people and they like colours, pictures, something attractive.
• Vertical design
• NO YELLOW or BLACK AS THE BACKGROUND COLOUR OF ANY SIDE OF THE BIZ CARD

```html
<!DOCTYPE html>
<html lang="en">
<head>
<meta charset="utf-8">
<title>Coastal Learner Bureau – Business Cards</title>
<link rel="stylesheet" href="https://fonts.googleapis.com/css2?family=Arimo:wght@400;700&display=swap">
<style>
  :root {
    --stage: #e9eaec;
    --card-white: #ffffff;
    --card-tint: #f1f2f1;
    --brand-green: #11654a;
    --green-deep: #0c4f39;
    --green-soft: #16775a;
    --brand-yellow: #e3bb14;
    --ink: #1d1d1b;
    --on-green: #ffffff;
    --sans: "Arimo", Arial, sans-serif;
  }
  * { box-sizing: border-box; margin: 0; padding: 0; }
  html, body {
    width: 1200px; height: 997px; overflow: hidden;
    background: var(--stage);
    font-family: var(--sans);
  }
  .stage { position: relative; width: 1200px; height: 997px; }

  .card {
    position: absolute; top: 348px;
    width: 525px; height: 300px;
    border-radius: 18px; overflow: hidden;
    box-shadow: 0 10px 28px rgba(0,0,0,.18);
  }

  /* Front */
  .card-front { left: 50px; background: var(--card-white); }
  .front-wash {
    position: absolute; inset: 0;
    background: radial-gradient(ellipse at 50% 45%, var(--card-white) 20%, var(--card-tint) 100%);
  }
  .front-brand {
    position: absolute; left: 0; right: 0; top: 102px;
    display: flex; align-items: center; justify-content: center; gap: 12px;
  }
  .brand-dot { width: 22px; height: 22px; border-radius: 50%; background: var(--brand-yellow); flex: none; }
  .brand-name {
    font-weight: 700; font-size: 34px; color: var(--brand-green); letter-spacing: .2px;
    white-space: nowrap;
  }
  .front-tagline {
    position: absolute; left: 0; right: 0; top: 178px; text-align: center;
    font-size: 17px; letter-spacing: 1.6px; color: var(--brand-green);
  }

  /* Back: green field, yellow used only as accent */
  .card-back { left: 625px; background: var(--brand-green); }
  .back-band {
    position: absolute; left: 0; right: 0; top: 0; height: 62px;
    background: var(--green-deep);
  }
  .back-body {
    position: absolute; inset: 62px 0 8px 0;
    background: linear-gradient(135deg, var(--green-soft) 0%, var(--brand-green) 60%);
  }
  .back-foot {
    position: absolute; left: 0; right: 0; bottom: 0; height: 8px;
    background: var(--brand-yellow);
  }
  .back-brand {
    position: absolute; top: 40px; left: 120px;
    display: flex; align-items: center; gap: 8px;
    background: var(--card-white); border-radius: 22px; padding: 8px 16px;
  }
  .back-brand .brand-dot { width: 14px; height: 14px; }
  .back-brand .brand-name { font-size: 19px; }

  .holder { position: absolute; right: 26px; top: 110px; text-align: right; }
  .holder-name { font-weight: 700; font-size: 17px; color: var(--brand-yellow); letter-spacing: .8px; }
  .holder-role { font-size: 11px; color: var(--on-green); margin-top: 2px; }
  .rule {
    position: absolute; left: 26px; right: 26px; top: 150px;
    height: 1.5px; background: var(--brand-yellow);
  }
  .contacts {
    position: absolute; left: 26px; bottom: 26px;
    list-style: none; display: flex; flex-direction: column; gap: 6px;
  }
  .contacts li { display: flex; align-items: center; gap: 8px; font-size: 13px; color: var(--on-green); }
  .contact-icon { width: 16px; height: 16px; flex: none; }
  .website {
    position: absolute; right: 26px; bottom: 30px;
    font-weight: 700; font-size: 14px; color: var(--brand-yellow); letter-spacing: 1px;
  }
</style>
</head>
<body>
<main class="stage">

  <section class="card card-front" aria-label="Business card front">
    <div class="front-wash"></div>
    <div class="front-brand">
      <span class="brand-dot"></span>
      <span class="brand-name">Coastal Learner Bureau</span>
    </div>
    <p class="front-tagline">¡HACEMOS MÁS POR TI</p>
  </section>

  <section class="card card-back" aria-label="Business card back">
    <div class="back-band"></div>
    <div class="back-body"></div>
    <div class="back-foot"></div>

    <div class="back-brand">
      <span class="brand-dot"></span>
      <span class="brand-name">Coastal Learner Bureau</span>
    </div>

    <div class="holder">
      <p class="holder-name">TOMAS BILBREA</p>
      <p class="holder-role">Managing Director</p>
    </div>
    <div class="rule"></div>

    <ul class="contacts">
      <li>
        <svg class="contact-icon" viewBox="0 0 16 16" aria-hidden="true"><circle cx="8" cy="8" r="8" fill="#e3bb14"/></svg>
        coastallearner
      </li>
      <li>
        <svg class="contact-icon" viewBox="0 0 16 16" aria-hidden="true">
          <circle cx="8" cy="8" r="8" fill="#e3bb14"/>
          <path d="M5.2 4.2l1.6 0 .6 2-1 .8c.5 1.1 1.3 1.9 2.4 2.4l.8-1 2 .6v1.6c0 .5-.5.9-1 .8C7.6 11 5 8.4 4.4 5.2c-.1-.5.3-1 .8-1z" fill="#11654a"/>
        </svg>
        +61 491058264
      </li>
      <li>
        <svg class="contact-icon" viewBox="0 0 16 16" aria-hidden="true">
          <circle cx="8" cy="8" r="8" fill="#e3bb14"/>
          <rect x="4" y="5.2" width="8" height="5.6" rx=".6" fill="#11654a"/>
          <path d="M4.3 5.5L8 8.4l3.7-2.9" fill="none" stroke="#e3bb14" stroke-width=".9"/>
        </svg>
        tomas@kelvarin.com.au
      </li>
    </ul>

    <p class="website">WWW.KELVORIA.COM.AU</p>
  </section>

</main>
</body>
</html>
```